General contractor/GM consaltant business card

I need a card for my contracting company in North Dakota, we build industrial buildings for the oil feild and oil feild related companies offices, shops, airplain hangars, airports ext. We have a familly atmosphere on the job and are very relational and personal.
Industry/Entity Type
Industrial
Contact Information for Business Card
Ridgepost Contractors LLC.
Derek T.Holloway
4837 Tamarind dr. Colorado Springs, CO. 80917
Cell# 406-555-0148
derek@ridgepostcontractors.com

```html
<!DOCTYPE html>
<html lang="en">
<head>
<meta charset="utf-8">
<title>Ridgepost Contractors LLC. – Business Card</title>
<link rel="stylesheet" href="https://fonts.googleapis.com/css2?family=Arimo:wght@400;700&display=swap">
<style>
  :root {
    --brand-blue: #0a22a8;
    --card-white: #ffffff;
    --ink: #2a2a2a;
    --band-text: #c9d2ff;
    --backdrop: #e6ebee;
  }
  * { margin: 0; padding: 0; box-sizing: border-box; }
  html, body {
    width: 1200px; height: 1200px; overflow: hidden;
    background: var(--backdrop);
    font-family: "Arimo", Arial, sans-serif;
  }
  .sheet {
    width: 1200px; height: 1200px;
    display: flex; flex-direction: column; align-items: center; justify-content: center;
    gap: 70px;
  }
  .card {
    position: relative;
    width: 840px; height: 480px;
    background: var(--card-white);
    box-shadow: 0 6px 18px rgba(0,0,0,0.12);
    overflow: hidden;
  }
  /* Front */
  .card-front__name {
    position: absolute; left: 70px; top: 72px;
    color: var(--brand-blue);
    font-weight: 700; font-size: 40px; letter-spacing: 5px;
  }
  .card-front__contact {
    position: absolute; left: 70px; top: 168px;
    list-style: none;
    color: var(--ink); font-size: 20px; line-height: 28px; letter-spacing: 1.5px;
  }
  .card-front__band {
    position: absolute; left: 0; right: 0; bottom: 0; height: 120px;
    background: var(--brand-blue);
    display: flex; justify-content: space-between; align-items: center;
    padding: 0 44px 0 70px;
  }
  .card-front__address {
    font-style: normal; color: var(--band-text);
    font-size: 18px; line-height: 26px; letter-spacing: 2px;
    align-self: flex-start; padding-top: 18px;
  }
  .company-name {
    color: var(--card-white); font-weight: 700; letter-spacing: 3px;
  }
  .card-front__band .company-name {
    font-size: 27px; line-height: 32px; text-align: left;
    align-self: flex-end; padding-bottom: 16px;
  }
  /* Back */
  .card-back { background: var(--brand-blue); }
  .card-back__strip {
    position: absolute; left: 0; top: 0; bottom: 0; width: 96px;
    background: var(--card-white);
  }
  .card-back .company-name {
    position: absolute; left: 96px; right: 0; top: 0; bottom: 0;
    display: flex; flex-direction: column; justify-content: center; align-items: center;
    font-size: 38px; line-height: 46px;
  }
</style>
</head>
<body>
<main class="sheet">
  <section class="card card-front" aria-label="Card front">
    <h1 class="card-front__name">Derek T.Holloway</h1>
    <ul class="card-front__contact">
      <li>406-555-0148</li>
      <li>derek@ridgepostcontractors.com</li>
      <li>www.ridgepostcontractors.com</li>
    </ul>
    <div class="card-front__band">
      <address class="card-front__address">4837 Tamarind dr. Colorado<br>Springs, CO. 80917</address>
      <p class="company-name">Ridgepost<br>Contractors LLC.</p>
    </div>
  </section>

  <section class="card card-back" aria-label="Card back">
    <div class="card-back__strip"></div>
    <p class="company-name"><span>Ridgepost</span><span>Contractors LLC.</span></p>
  </section>
</main>
</body>
</html>
```